Seeking funky, innovative business cards

I am looking to refresh our current business cards to something more engaging, visual and impactful. We are a management consultancy firm, see website (www.larkstone-partners.com.au). I've included our colour scheme, sample of the slides we use and our old business cards. We would like our cards to have icons. The card should display:- Name- Title- Mobile number- Address- Email address- Website - Company logo- Our purpose statement "We create the best places on earth to work"

Contact Information for Business Card

Brennan Ulfsson
Consultant
0468 927 341
Level 3, 218 Wexley Street, Melbourne 3000
brennan@larkstone-partners.com.au
www.larkstone-partners.com.au

Purpose statement "we create the best places on earth to work"
LOGO available in google images

Font styles to use
Other font styles liked:
• Open Sans Light, Bebas Neue (open to other cool foints)

Colors
ffc214
5c5c5c
f5f5f5
fefefe

Requirements
Must have
• - Name
• - Title
• - Mobile number
• - Address
• - Email address
• - Website
• - Company logo
• - Our purpose statement "We create the best places on earth to work"
Nice to have
• - Icons
• - Colour (see our colour scheme"

```html
<!DOCTYPE html>
<html lang="en">
<head>
<meta charset="utf-8">
<title>Larkstone Partners – Business Card</title>
<link rel="stylesheet" href="https://fonts.googleapis.com/css2?family=Lato:wght@400;700&family=Montserrat:wght@400;700&display=swap">
<style>
  :root {
    --stage: #26292b;
    --charcoal: #46494b;
    --paper: #ffffff;
    --ink: #3c3f41;
    --gold: #ffc214;
    --amber: #f7a833;
    --line-gold: #f2b81a;
  }
  * { margin: 0; padding: 0; box-sizing: border-box; }
  html, body {
    width: 1200px; height: 738px; overflow: hidden;
    background: var(--stage);
    font-family: "Lato", sans-serif;
  }
  .canvas { position: relative; width: 1200px; height: 738px; }

  .card {
    position: absolute;
    width: 480px; height: 294px;
    overflow: hidden;
    box-shadow: 0 18px 40px rgba(0,0,0,0.45);
  }

  /* Back of card */
  .card-back {
    left: 90px; top: 110px;
    background: var(--charcoal);
    text-align: center;
  }
  .card-back .brand {
    position: absolute; left: 0; right: 0; top: 100px;
    font-family: "Montserrat", sans-serif;
    font-weight: 400;
    font-size: 38px;
    letter-spacing: 0.5px;
    color: var(--paper);
  }
  .card-back .purpose {
    position: absolute; left: 0; right: 0; top: 232px;
    font-size: 14px;
    letter-spacing: 0.6px;
    color: var(--gold);
  }

  /* Front of card */
  .card-front {
    left: 630px; top: 334px;
    background: var(--paper);
  }
  .card-front .brand {
    position: absolute; right: 26px; top: 40px;
    display: flex; align-items: center; gap: 7px;
    font-family: "Montserrat", sans-serif;
    font-weight: 400;
    font-size: 22px;
    line-height: 26px;
    color: var(--ink);
  }
  .brand-dot {
    width: 9px; height: 9px; border-radius: 50%;
    background: var(--amber);
  }
  .holder-name {
    position: absolute; left: 22px; top: 88px;
    font-family: "Montserrat", sans-serif;
    font-weight: 700;
    font-size: 19px;
    line-height: 22px;
    letter-spacing: 1.2px;
    color: var(--gold);
  }
  .holder-title {
    position: absolute; left: 23px; top: 112px;
    font-size: 12px;
    line-height: 14px;
    color: var(--ink);
  }
  .rule {
    position: absolute; left: 22px; right: 26px; top: 132px;
    height: 1px; background: var(--line-gold);
  }
  .contacts {
    position: absolute; left: 22px; top: 144px;
    list-style: none;
  }
  .contacts li {
    display: flex; align-items: center; gap: 9px;
    height: 17px;
    font-size: 12.5px;
    color: var(--ink);
  }
  .contacts svg { width: 9px; height: 9px; fill: none; stroke: var(--amber); stroke-width: 1.6; }
  .contacts .solid { fill: var(--amber); stroke: none; }

  .wave { position: absolute; left: 0; top: 0; width: 480px; height: 294px; }
  .address {
    position: absolute; right: 26px; top: 230px;
    text-align: right;
    font-style: normal;
    font-size: 12.5px;
    line-height: 17px;
    color: var(--paper);
  }
</style>
</head>
<body>
<main class="canvas">

  <section class="card card-back" aria-label="Card back">
    <p class="brand">Larkstone Partners</p>
    <p class="purpose">We create the best places on earth to work</p>
  </section>

  <section class="card card-front" aria-label="Card front">
    <svg class="wave" viewBox="0 0 480 294" aria-hidden="true">
      <path d="M0,218 C110,252 210,248 305,204 C385,168 435,160 480,160 L480,294 L0,294 Z" fill="var(--amber)"/>
      <path d="M0,248 C115,278 225,254 322,212 C392,184 440,176 480,176 L480,294 L0,294 Z" fill="var(--paper)"/>
      <path d="M0,258 C115,290 225,266 322,224 C392,196 440,186 480,185 L480,294 L0,294 Z" fill="var(--charcoal)"/>
    </svg>

    <div class="brand"><span class="brand-dot"></span>Larkstone Partners</div>

    <h1 class="holder-name">BRENNAN ULFSSON</h1>
    <p class="holder-title">Consultant</p>
    <div class="rule"></div>

    <ul class="contacts">
      <li>
        <svg viewBox="0 0 10 10"><rect class="solid" x="2.5" y="0.5" width="5" height="9" rx="1"/></svg>
        0468 927 341
      </li>
      <li>
        <svg viewBox="0 0 10 10"><rect x="0.8" y="2" width="8.4" height="6"/><path d="M0.8,2 L5,5.5 L9.2,2"/></svg>
        brennan@larkstone-partners.com.au
      </li>
      <li>
        <svg viewBox="0 0 10 10"><circle cx="5" cy="5" r="4.2"/><path d="M0.8,5 H9.2 M5,0.8 C2.6,3.4 2.6,6.6 5,9.2 M5,0.8 C7.4,3.4 7.4,6.6 5,9.2"/></svg>
        www.larkstone-partners.com.au
      </li>
    </ul>

    <address class="address">
      Level 3, 218 Wexley Street<br>
      Melbourne 3000
    </address>
  </section>

</main>
</body>
</html>
```